Luxury Real Estate Website, Midwest, United States

We need web design services for a luxury website. We need IDX Integration with our MLS. We want this to be a very simple website with amazing graphics. We want it to link up with our (mascot illustration replaced by flat placeholder) account in order to generate leads through a "More Information" Pop up on the main page. We want the main page to be covered with one large graphic that is a rolling slideshow of active listings of $400,000 and up from the IDX Integration. We need this website to give a very exclusive and sleek look. Lots of black is good... I will upload our logos in Black and Silver. We will also need an "About" page that we are going to call "Qeno Info". We want our graphics to be extremely impressive. Keep in mind, we are a company in the Midwest of the United States, and our real estate has a different look than homes in California or Florida. We need graphics that are realistic for the Midwest, yet still high-end.
Target Market(s)
Luxury Homeowners in the Midwest United States. The graphics needs to be pristine.
Industry/Entity Type
Real Estate
Coding
Coded - Design and coding required
Number of Pages Required
3 page
Requirements
Must have
- Large graphics with IDX Integration. The photos of real estate need to represent real estate that is common in the Midwest, United States. We also need (mascot illustration replaced by flat placeholder) integration. We need a pop up that is titled "My Free Market Analysis" that makes them fill out a contact form asking for Full Name, Email Address, Phone Number and Address. This needs to be a pop up on the front page and will integrate with our (mascot illustration replaced by flat placeholder) account. We also need a page called "About Qe No Home". And another page where clients can download informational PDFs. The main component needs to be a front page search engine connected with the IDX to access active listings from our MLS. I attached our logos and a sample front page of a website. I would love for ours to look similar.
Nice to have
- Lake House photos on midwest lakes are a plus.
Should not have
- Should not have clutter. This website needs to be clean, luxurious and exclusive.

```html
<!DOCTYPE html>
<html lang="en">
<head>
<meta charset="utf-8">
<title>Harbor Crest Realty Group</title>
<link href="https://fonts.googleapis.com/css2?family=Poppins:wght@400;500&family=Open+Sans:wght@400;600&display=swap" rel="stylesheet">
<style>
:root{
  --ink:#222;
  --muted:#8a8a8a;
  --header:#f4f4f4;
  --accent:#3d5f9c;
  --band:#3f4f63;
  --footer:#1b1b1b;
  --footer-text:#bdbdbd;
  --card-border:#e4e4e4;
  --btn-dark:#3a4450;
  --submit:#8fb0d8;
  --veil:rgba(0,0,0,.62);
}
*{box-sizing:border-box;margin:0;padding:0}
html,body{width:1200px;height:2553px;overflow:hidden}
body{position:relative;background:#fff;font-family:'Open Sans',Arial,sans-serif;color:var(--ink)}
.page{position:absolute;inset:0}
.abs{position:absolute}
.brand{font-family:'Poppins',Arial,sans-serif;font-weight:500;color:#1d1d1d;line-height:1.05;letter-spacing:1px}

/* header */
.site-header{left:0;top:0;width:1200px;height:106px;background:var(--header)}
.site-header .brand{left:85px;top:28px;font-size:27px}
.site-header .brand small{display:block;font-size:13px;letter-spacing:3px}
.nav a{position:absolute;top:44px;font-family:'Poppins',Arial,sans-serif;font-size:13px;color:#333;text-decoration:none;transform:translateX(-50%);white-space:nowrap}

/* hero */
.hero{left:0;top:106px;width:1200px;height:544px;background:linear-gradient(180deg,#8a98a8 0%,#5f6a58 55%,#3e5232 100%)}
.search-panel{left:260px;top:361px;width:681px;height:95px;background:rgba(0,0,0,.45)}
.search-panel h2{position:absolute;left:23px;top:10px;font-family:'Poppins',Arial,sans-serif;font-weight:400;font-size:21px;color:#fff}
.search-input{position:absolute;left:23px;top:53px;width:636px;height:42px;background:#fff;font-size:12px;color:#999;padding:13px 14px}
.search-input svg{position:absolute;right:14px;top:12px}

/* about */
.about-photo-a{left:0;top:732px;width:536px;height:357px;background:linear-gradient(160deg,#7d8a99,#3f6f8a 60%,#2e4a5c)}
.about-photo-b{left:311px;top:929px;width:285px;height:240px;background:linear-gradient(160deg,#9b3a36,#6e5a4c 60%,#4a3b30)}
.about-text{left:689px;top:745px;width:420px}
.about-text h1{font-family:'Poppins',Arial,sans-serif;font-weight:500;font-size:34px;color:#333;white-space:nowrap;margin-left:-150px}
.about-text .sub{font-size:14px;color:var(--accent);margin-top:12px}
.about-text p{font-size:12px;line-height:26px;color:#999;margin-top:16px}
.about-text p + p{margin-top:26px}
.btn-outline{display:inline-block;margin-top:30px;width:190px;height:44px;border:1px solid #555;font-size:14px;color:#444;text-align:center;line-height:42px}

/* features */
.feature{width:300px;text-align:center;transform:translateX(-50%);top:1250px}
.feature h3{font-family:'Poppins',Arial,sans-serif;font-weight:400;font-size:17px;color:#444;margin-top:14px}
.feature p{font-size:12px;line-height:26px;color:#999;margin-top:6px}

/* featured property */
.featured-title{left:0;width:1200px;top:1502px;text-align:center;font-family:'Poppins',Arial,sans-serif;font-weight:500;font-size:28px;color:#222}
.featured-sub{left:0;width:1200px;top:1549px;text-align:center;font-size:12px;color:#999}
.card{top:1595px;width:329px;height:417px;border:1px solid var(--card-border);text-align:center}
.card .photo{margin:7px;height:197px}
.card h3{font-family:'Poppins',Arial,sans-serif;font-weight:400;font-size:18px;color:#333;margin-top:24px}
.card p{font-size:12px;line-height:26px;color:#999;padding:0 34px;margin-top:8px}
.card .btn{display:inline-block;margin-top:18px;width:112px;height:37px;background:var(--btn-dark);color:#ccc;font-size:14px;line-height:37px}

/* banner */
.band{left:0;top:2059px;width:1200px;height:244px;background:var(--band);text-align:center;color:#fff}
.band h2{margin-top:57px;font-family:'Poppins',Arial,sans-serif;font-weight:400;font-size:24px;letter-spacing:.5px}
.band p{font-family:'Poppins',Arial,sans-serif;font-size:21px;margin-top:6px}
.band .btn-ghost{display:inline-block;margin-top:22px;width:208px;height:46px;border:1px solid #fff;font-size:18px;line-height:44px}

/* footer */
.site-footer{left:0;top:2303px;width:1200px;height:250px;background:var(--footer);color:var(--footer-text)}
.site-footer .brand{color:#e8e8e8;left:145px;top:75px;font-size:34px}
.site-footer .brand small{display:block;font-size:15px;letter-spacing:4px}
.site-footer h4{font-family:'Poppins',Arial,sans-serif;font-weight:500;font-size:16px;color:#e0e0e0}
.site-footer a{position:absolute;font-size:12px;color:var(--footer-text);text-decoration:none}
.newsletter-input{left:764px;top:109px;width:337px;height:44px;background:#fff;font-size:12px;color:#999;padding:14px 16px}
.newsletter-btn{left:1057px;top:109px;width:44px;height:44px;background:#555}
.copyright{left:0;width:1200px;top:208px;text-align:center;font-size:12px}

/* modal */
.veil{position:absolute;inset:0;background:var(--veil)}
.modal{left:356px;top:289px;width:529px;height:547px;background:#fff}
.modal .mascot{position:absolute;left:15px;top:17px;width:123px;height:137px;background:linear-gradient(160deg,#6b4a32,#2f4f9a);border-radius:8px}
.modal .brand{position:absolute;left:155px;top:36px;font-size:27px}
.modal .brand small{display:block;font-size:13px;letter-spacing:3px}
.modal h2{position:absolute;left:151px;top:108px;font-family:'Poppins',Arial,sans-serif;font-weight:400;font-size:27px;color:#222;white-space:nowrap}
.field{position:absolute;left:86px;width:368px;border:1px solid #c9c9c9;font-size:12px;color:#333;padding:12px 9px}
.submit{position:absolute;left:200px;top:465px;width:128px;height:39px;background:var(--submit);color:#fff;font-family:'Poppins',Arial,sans-serif;font-size:15px;text-align:center;line-height:39px}
.close{left:851px;top:274px;width:56px;height:56px;border-radius:50%;background:#1e1e1e;border:3px solid #fff;color:#fff;font-family:'Poppins',Arial,sans-serif;font-size:18px;text-align:center;line-height:48px}
</style>
</head>
<body>
<div class="page">
  <header class="abs site-header">
    <div class="abs brand">HARBOR CREST<small>REALTY GROUP</small></div>
    <nav class="nav">
      <a style="left:536px">HOME</a>
      <a style="left:638px">QENO INFO</a>
      <a style="left:785px">ABOUT QE NO HOME</a>
      <a style="left:940px">DOWNLOADS</a>
      <a style="left:1072px">CONTACT US</a>
    </nav>
  </header>

  <section class="abs hero" role="img" aria-label="Photo of a large Midwest family home at dusk"></section>
  <div class="abs search-panel">
    <h2>Home Finder</h2>
    <div class="search-input">Enter Your City, Address or MLS #
      <svg width="18" height="18" viewBox="0 0 18 18"><circle cx="7.5" cy="7.5" r="5.5" fill="none" stroke="#888" stroke-width="2"/><line x1="11.5" y1="11.5" x2="16" y2="16" stroke="#888" stroke-width="2"/></svg>
    </div>
  </div>

  <div class="abs about-photo-a" role="img" aria-label="Photo of lake houses along a waterfront"></div>
  <div class="abs about-photo-b" role="img" aria-label="Photo of a family on a porch of a red house"></div>
  <div class="abs about-text">
    <h1>HARBOR CREST REALTY GROUP</h1>
    <div class="sub">Luxury Homes Across the Midwest, United States</div>
    <p>Sed ut perspiciatis unde omnis iste natus error sit voluptatem accusanti um doloremque laudantium, totam rem aperiam, eaque ipsa quae ab illo inventore veritatis et quasi architecto beatae vitae dicta sunt explicabo. Nemo enim ipsam voluptatem quia voluptas sit aspernatur.</p>
    <p>Sed ut perspiciatis unde omnis iste natus error sit voluptatem accusanti um doloremque laudantium, totam rem aperiam, eaque ipsa quae ab illo inventore veritatis et quasi architecto beatae vitae dicta sunt explicabo. Nemo enim ipsam voluptatem quia voluptas sit aspernatur.</p>
    <span class="btn-outline">Click Here For More Info</span>
  </div>

  <div class="abs feature" style="left:250px">
    <svg width="62" height="56" viewBox="0 0 62 56" fill="none" stroke="#555" stroke-width="2"><path d="M6 50h50M10 50V28l21-16 21 16v22M22 50V36h18v14"/><path d="M3 54h56"/></svg>
    <h3>Contrary to Popular</h3>
    <p>Sed ut perspiciatis unde omnis iste natus error sit voluptatem accusanti um doloremque</p>
  </div>
  <div class="abs feature" style="left:601px">
    <svg width="62" height="56" viewBox="0 0 62 56" fill="none" stroke="#555" stroke-width="2"><path d="M16 4c-6 9-9 14-9 18a9 9 0 0018 0c0-4-3-9-9-18z"/><path d="M6 38c6-4 10 4 16 0s10 4 16 0 10 4 16 0M6 46c6-4 10 4 16 0s10 4 16 0 10 4 16 0M6 54c6-4 10 4 16 0s10 4 16 0 10 4 16 0"/></svg>
    <h3>Contrary to Popular</h3>
    <p>Sed ut perspiciatis unde omnis iste natus error sit voluptatem accusanti um doloremque</p>
  </div>
  <div class="abs feature" style="left:950px">
    <svg width="68" height="56" viewBox="0 0 68 56" fill="#555"><path d="M30 22L48 6l18 16h-5v16H35V22z" fill="none" stroke="#555" stroke-width="2"/><circle cx="22" cy="26" r="8"/><path d="M6 54c0-12 7-18 16-18s16 6 16 18z"/><circle cx="40" cy="34" r="6"/><path d="M30 54c0-9 5-13 10-13s10 4 10 13z"/></svg>
    <h3>Contrary to Popular</h3>
    <p>Sed ut perspiciatis unde omnis iste natus error sit voluptatem accusanti um doloremque</p>
  </div>

  <h2 class="abs featured-title">OUR FEATURED PROPERTY</h2>
  <p class="abs featured-sub">Sed ut perspiciatis unde omnis iste natus error sit voluptatem accusanti um doloremque laudantium, totam rem aperiam.</p>

  <article class="abs card" style="left:85px">
    <div class="photo" role="img" aria-label="Photo of a lakeside cottage among pine trees" style="background:linear-gradient(160deg,#6f8a9b,#3d5a3a 60%,#2b3a2a)"></div>
    <h3>Sed ut perspiciatis unde</h3>
    <p>Nemo enim ipsam voluptatem quia voluptas sit asper natur aut odit aut fugit, sed quia consequuntur magni ratione voluptatem sequi nesciunt.</p>
    <span class="btn">Read More</span>
  </article>
  <article class="abs card" style="left:434px">
    <div class="photo" role="img" aria-label="Photo of a large grey two-storey house by a pond" style="background:linear-gradient(160deg,#93a4b3,#5f6f74 55%,#3f5a3a)"></div>
    <h3>Sed ut perspiciatis unde</h3>
    <p>Nemo enim ipsam voluptatem quia voluptas sit asper natur aut odit aut fugit, sed quia consequuntur magni ratione voluptatem sequi nesciunt.</p>
    <span class="btn">Read More</span>
  </article>
  <article class="abs card" style="left:783px">
    <div class="photo" role="img" aria-label="Photo of a red lake house with a dock" style="background:linear-gradient(160deg,#4f6a3e,#8a3a2e 55%,#3a4a33)"></div>
    <h3>Sed ut perspiciatis unde</h3>
    <p>Nemo enim ipsam voluptatem quia voluptas sit asper natur aut odit aut fugit, sed quia consequuntur magni ratione voluptatem sequi nesciunt.</p>
    <span class="btn">Read More</span>
  </article>

  <section class="abs band">
    <h2>SED UT PERSPICIATIS UNDE OMNIS ISTE NATUS ERROR SIT VOLUPTATEM</h2>
    <p>accusantium doloremque laudantium, totam rem aperiam</p>
    <span class="btn-ghost">Downloads</span>
  </section>

  <footer class="abs site-footer">
    <div class="abs brand">HARBOR CREST<small>REALTY GROUP</small></div>
    <h4 class="abs" style="left:453px;top:28px">QUICK LINKS</h4>
    <a style="left:455px;top:72px">Home</a>
    <a style="left:455px;top:101px">Qeno Info</a>
    <a style="left:455px;top:130px">About Qe No Home</a>
    <a style="left:613px;top:72px">Downloads</a>
    <a style="left:613px;top:101px">Contact us</a>
    <h4 class="abs" style="left:763px;top:28px">NEWSLETTER</h4>
    <p class="abs" style="left:763px;top:72px;font-size:12px">Sed ut perspiciatis unde omnis iste natus error sit</p>
    <div class="abs newsletter-input">Enter Your Email Id</div>
    <div class="abs newsletter-btn"><svg width="44" height="44" viewBox="0 0 44 44"><path d="M14 22l16-8-5 17-3-6z" fill="none" stroke="#ddd" stroke-width="1.5"/></svg></div>
    <p class="abs copyright">© Copy Right -2018 Harbor Crest Realty Group All rights reserved.</p>
  </footer>
</div>

<div class="veil"></div>

<div class="abs modal" role="dialog" aria-label="My Free Market Analysis">
  <div class="mascot" role="img" aria-label="Mascot illustration carrying a mail bag"></div>
  <div class="brand">HARBOR CREST<small>REALTY GROUP</small></div>
  <h2>My Free Market Analysis</h2>
  <div class="field" style="top:193px;height:43px">Full Name :</div>
  <div class="field" style="top:244px;height:43px">Email Address :</div>
  <div class="field" style="top:296px;height:43px">Phone Number :</div>
  <div class="field" style="top:349px;height:96px">Address :</div>
  <div class="submit">SUBMIT</div>
</div>
<div class="abs close">x</div>
</body>
</html>
```